Business Card Design For A Cajun Seafood Restaurant

We are opening a cajun seafood restaurant in a week. We mainly serve cajun seafood which is orginally from Louisiana. We want design on both sides of a business card. I have menu on the website. You can go to www.reednkettle.example to check out our menu.

Restaurant name: Reed N' Kettle
Phone: +1 (555) 304-7712
Address: 48206 Ludlow Row, #7, Bexmoor Flats, Ca90000
Email: reednkettle@mailbox.example
Website: www.reednkettle.example

Maybe add social media icons (facebook, instagram) if looks nice on the business card.
facebook.com/reednkettle
instagram.com/reednkettle or @reednkettle

Attached is the logo and other business card samples that I like.

```html
<!DOCTYPE html>
<html lang="en">
<head>
<meta charset="utf-8">
<title>Reed N' Kettle — Business Card</title>
<link rel="stylesheet" href="https://fonts.googleapis.com/css2?family=Lato:wght@400;700;900&display=swap">
<style>
  :root {
    --bg: #b9b9b9;
    --card-white: #ffffff;
    --card-black: #050505;
    --ink: #111111;
    --orange: #f2651a;
    --orange-deep: #d94e0f;
    --yellow: #f7d417;
    --corn: #f3c21a;
    --muted: #2a2a2a;
  }
  * { box-sizing: border-box; margin: 0; padding: 0; }
  html, body { width: 1200px; height: 837px; overflow: hidden; }
  body {
    background: var(--bg);
    font-family: "Lato", Arial, sans-serif;
    color: var(--ink);
    position: relative;
  }
  .card {
    position: absolute;
    width: 532px;
    height: 304px;
    top: 266px;
    box-shadow: 0 10px 26px rgba(0,0,0,.22);
  }
  .card-back {
    left: 54px;
    background: var(--card-black);
    display: flex;
    align-items: center;
    justify-content: center;
  }
  .back-mark {
    display: flex;
    align-items: center;
    gap: 14px;
  }
  .back-mark__dot {
    width: 22px; height: 22px;
    border-radius: 50%;
    background: var(--orange);
  }
  .back-mark__name {
    font-weight: 900;
    font-size: 40px;
    color: var(--yellow);
    letter-spacing: 0.5px;
  }
  .back-tagline {
    position: absolute;
    left: 0; right: 0; bottom: 88px;
    text-align: center;
    font-weight: 700;
    font-size: 13px;
    letter-spacing: 3px;
    color: var(--card-white);
  }
  .card-front {
    left: 614px;
    background: var(--card-white);
  }
  .mascot {
    position: absolute;
    left: 14px; top: 20px;
    width: 236px; height: 264px;
    border-radius: 46% 40% 44% 48%;
    background: radial-gradient(circle at 55% 30%, var(--corn) 0 18%, var(--orange) 40%, var(--orange-deep) 75%);
  }
  .details {
    position: absolute;
    left: 272px; top: 44px;
    width: 240px;
  }
  .brand {
    font-weight: 900;
    font-size: 30px;
    color: var(--orange);
    line-height: 1;
    margin-bottom: 18px;
  }
  .person__name {
    font-weight: 700;
    font-size: 17px;
    color: var(--orange);
  }
  .person__role {
    font-size: 12px;
    color: var(--muted);
    margin-bottom: 16px;
  }
  .contact {
    list-style: none;
    font-size: 12px;
    line-height: 1.55;
    color: var(--ink);
  }
  .contact li { display: flex; align-items: center; gap: 7px; }
  .icon {
    width: 14px; height: 14px;
    background: var(--orange);
    border-radius: 2px;
    flex: none;
    display: inline-flex; align-items: center; justify-content: center;
  }
  .icon--none { background: transparent; }
  .site { margin-top: 4px; font-size: 12px; }
  .site__core { color: var(--orange); }
  .social {
    margin-top: 10px;
    display: flex; align-items: center; gap: 8px;
    font-size: 12px;
  }
  .social__square {
    width: 16px; height: 16px;
    background: var(--orange);
    border-radius: 2px;
  }
</style>
</head>
<body>

  <section class="card card-back" aria-label="Card back">
    <div class="back-mark">
      <span class="back-mark__dot"></span>
      <span class="back-mark__name">Reed N' Kettle</span>
    </div>
    <p class="back-tagline">CAJUN SEAFOOD HOUSE</p>
  </section>

  <section class="card card-front" aria-label="Card front">
    <div class="mascot" role="img" aria-label="Illustration of a cheerful orange crab holding an ear of yellow corn"></div>

    <div class="details">
      <h1 class="brand">Reed N' Kettle</h1>

      <p class="person__name">Dale Mercer</p>
      <p class="person__role">Managing Director</p>

      <ul class="contact">
        <li><span class="icon icon--none"></span>48206 Ludlow Row, #7</li>
        <li><span class="icon icon--none"></span>Bexmoor Flats, Ca90000</li>
        <li>
          <span class="icon">
            <svg width="9" height="9" viewBox="0 0 10 10"><path d="M2 1 L4 1 L4.6 3.2 L3.5 4 Q4.3 5.8 6 6.5 L6.8 5.4 L9 6 L9 8 Q8.6 9 7.5 9 Q1 8.4 1 2.5 Q1 1 2 1Z" fill="#fff"/></svg>
          </span>+1 (555) 304-7712
        </li>
        <li>
          <span class="icon">
            <svg width="10" height="8" viewBox="0 0 10 8"><rect x="0.5" y="0.5" width="9" height="7" fill="none" stroke="#fff"/><path d="M0.5 0.5 L5 4.5 L9.5 0.5" fill="none" stroke="#fff"/></svg>
          </span>reednkettle@mailbox.example
        </li>
      </ul>

      <p class="site">www.<span class="site__core">reednkettle</span>.example</p>

      <div class="social">
        <span class="social__square"></span>
        <span>reednkettle</span>
      </div>
    </div>
  </section>

</body>
</html>
```